New web page, 2 companies on the one page

A new web page for an engineering consultancy and maintenance management company

Corlett & Associates is the parent company covering the design and consultancy
Valtrix Engineering is the Maintenance and Reliability company

Target Market(s)

Food & Beverage, ingredients Manufacturing
engineering managers

Coding

Coded - Design and coding required

Number of Pages Required

1 page

Font styles to use
Other font styles liked:
• Roboto

Colors
1861ab
85acd3
d0dfed
cee9f5

```html
<!DOCTYPE html>
<html lang="en">
<head>
<meta charset="utf-8">
<title>Corlett &amp; Associates</title>
<link href="https://fonts.googleapis.com/css2?family=Jost:wght@400;500;600;700;800&display=swap" rel="stylesheet">
<style>
:root{
  --brand:#1e9fdb;
  --brand-deep:#1861ab;
  --brand-band:#29a9e2;
  --ink:#2b2b2b;
  --muted:#555;
  --grey-band:#ebebeb;
  --footer:#1b1b1d;
  --white:#fff;
}
*{margin:0;padding:0;box-sizing:border-box}
html,body{width:1200px;height:3442px;overflow:hidden}
body{font-family:"Jost",sans-serif;color:var(--ink);background:var(--white);position:relative}
.abs{position:absolute}
.center{text-align:center}

/* header */
.site-header{position:absolute;left:0;top:0;width:1200px;height:111px;background:var(--white)}
.brand{position:absolute;left:111px;top:33px;width:240px;display:flex;align-items:center;gap:10px;white-space:nowrap}
.brand-mark{width:40px;height:40px;background:var(--brand);flex:none}
.brand-name{font-size:20px;font-weight:700;color:#333;letter-spacing:.3px;line-height:1}
.main-nav{position:absolute;top:46px;left:424px;display:flex;gap:40px;font-size:14px;font-weight:500;color:#444;text-transform:uppercase;white-space:nowrap}
.main-nav .active{color:var(--brand);position:relative}
.main-nav .active::after{content:"";position:absolute;left:0;right:0;top:30px;height:3px;background:var(--brand)}

/* hero */
.hero{position:absolute;left:0;top:111px;width:1200px;height:594px;background:linear-gradient(100deg,#9aa1a8 0%,#6f757c 45%,#3e4348 75%,#2b2f33 100%)}
.hero-title{position:absolute;left:0;width:1200px;top:200px;font-size:86px;line-height:1;font-weight:700;color:var(--white);letter-spacing:1px;white-space:nowrap}
.hero-sub{position:absolute;left:0;width:1200px;top:290px;font-size:21px;line-height:1.3;color:var(--white);white-space:nowrap}
.hero-arrow{position:absolute;top:228px;width:48px;height:48px;border-radius:50%}
.hero-arrow.prev{left:29px;background:rgba(255,255,255,.18)}
.hero-arrow.next{left:1110px}

/* about */
.about{position:absolute;left:0;top:705px;width:1200px;height:418px;background:linear-gradient(180deg,#f4f5f7,#e9ecef)}
.section-title{font-size:35px;line-height:1.2;font-weight:700;color:var(--brand);text-transform:uppercase;width:1200px;left:0}
.about .section-title{top:62px}
.about-text{position:absolute;left:195px;width:810px;font-size:14px;line-height:27px;color:#333;text-align:center}
.btn{position:absolute;height:39px;border-radius:4px;font-size:14px;font-weight:700;text-transform:uppercase;display:flex;align-items:center;justify-content:center}
.btn-solid{background:var(--brand);color:var(--white)}
.btn-light{background:var(--white);color:var(--brand)}

/* services */
.services{position:absolute;left:0;top:1123px;width:1200px;height:544px;background:var(--grey-band)}
.services .section-title{top:50px}
.service{position:absolute;top:135px;width:220px;text-align:center}
.service-icon{width:130px;height:130px;margin:0 auto;border:3px solid var(--brand);border-radius:50%;display:flex;align-items:center;justify-content:center}
.service-title{font-size:15px;font-weight:600;color:#333;margin-top:14px;line-height:20px;min-height:40px;display:flex;align-items:center;justify-content:center}
.service-text{font-size:12px;line-height:20px;color:#444;margin-top:6px}

/* projects */
.projects{position:absolute;left:0;top:1667px;width:1200px;height:901px;background:var(--brand-band)}
.projects .section-title{top:58px;color:var(--white)}
.projects-intro{position:absolute;left:200px;width:800px;top:116px;font-size:14px;line-height:21px;color:var(--white);text-align:center}
.project-tile{position:absolute;width:314px;height:251px}

/* reviews */
.reviews{position:absolute;left:0;top:2568px;width:1200px;height:528px;background:linear-gradient(180deg,#f3f4f6,#eceef1)}
.reviews .section-title{top:68px}
.avatar{position:absolute;left:536px;top:133px;width:128px;height:128px;border-radius:50%;border:4px solid var(--white);background:linear-gradient(160deg,#8d9aa8,#3b4a5c)}
.quote-text{position:absolute;left:240px;width:720px;top:284px;font-size:14px;line-height:23px;color:#555;text-align:center}
.quote-mark{position:absolute;font-size:60px;color:#c9ccd0;font-family:Georgia,serif;line-height:1}
.reviewer{position:absolute;left:0;width:1190px;top:376px;text-align:center}
.reviewer-name{font-size:20px;font-weight:700;color:var(--brand);text-transform:uppercase}
.reviewer-role{font-size:14px;color:#555;text-transform:uppercase}
.dots{position:absolute;top:473px;left:565px;display:flex;gap:11px}
.dots span{width:6px;height:6px;border-radius:50%;background:#b8bec4}
.dots .on{background:var(--brand)}

/* footer */
.site-footer{position:absolute;left:0;top:3096px;width:1200px;height:346px;background:var(--footer);color:var(--white)}
.footer-brand{position:absolute;left:111px;top:64px;display:flex;align-items:center;gap:12px;white-space:nowrap}
.footer-brand .brand-mark{width:40px;height:40px}
.footer-brand .brand-name{color:var(--white);font-size:22px}
.socials{position:absolute;left:190px;top:170px;display:flex;gap:9px}
.socials span{width:34px;height:34px;border-radius:50%;background:#4a4b4f}
.footer-heading{position:absolute;top:60px;font-size:16px;font-weight:700;text-transform:uppercase}
.footer-links{position:absolute;top:100px;font-size:12px;line-height:30px}
.contact{position:absolute;left:903px;top:100px;font-size:12px;width:200px}
.contact-row{display:flex;gap:7px;align-items:flex-start}
.contact-strong{font-size:15px;font-weight:600}
.footer-rule{position:absolute;left:111px;top:269px;width:978px;height:1px;background:#333}
.copyright{position:absolute;left:0;width:1200px;top:296px;font-size:11px;text-align:center;color:#ddd}
</style>
</head>
<body>

<header class="site-header">
  <div class="brand"><span class="brand-mark"></span><span class="brand-name">Corlett &amp; Associates</span></div>
  <nav class="main-nav">
    <span class="active">Home</span><span>About Us</span><span>Services</span><span>Our Projects</span><span>Client Reviews</span><span>Contact Us</span>
  </nav>
</header>

<section class="hero" role="img" aria-label="Photo of a businessman in a suit holding a tablet beside a window overlooking a city skyline">
  <h1 class="hero-title center">CORLETT ASSOCIATES</h1>
  <p class="hero-sub center">We are an engineering consultancy and maintenance management company from Australia.</p>
  <span class="hero-arrow prev"><svg width="48" height="48" viewBox="0 0 48 48"><path d="M28 13 L18 24 L28 35" fill="none" stroke="#fff" stroke-width="1.5"/></svg></span>
  <span class="hero-arrow next"><svg width="48" height="48" viewBox="0 0 48 48"><path d="M20 13 L30 24 L20 35" fill="none" stroke="#fff" stroke-width="1.5"/></svg></span>
</section>

<section class="about">
  <h2 class="section-title abs center">About Corlett Associates</h2>
  <p class="about-text" style="top:119px">Corlett &amp; Associates is specialised manufacturing engineering support organisation that can provide fast, nimble, and flexible services. We have a proven track record in delivering tangible outcomes in process design and fit-out, project management, manufacturing process and maintenance design and execution.</p>
  <p class="about-text" style="top:214px">Our specialist focus in food manufacturing across a range of sectors allows our team to deliver real benefits to performance and recognition of the clients investment</p>
  <span class="btn btn-solid" style="left:534px;top:304px;width:132px">Read More</span>
</section>

<section class="services">
  <h2 class="section-title abs center">Our Services</h2>
  <div class="service" style="left:108px">
    <div class="service-icon"><svg width="64" height="64" viewBox="0 0 64 64" fill="none" stroke="#1e9fdb" stroke-width="2.5"><circle cx="32" cy="26" r="12"/><path d="M26 40h12M27 46h10M29 52h6"/></svg></div>
    <div class="service-title">Process &amp; Facilities Design</div>
    <p class="service-text">Lorem ipsum dolor sit amet, consectetur adipiscing elit, sed do eiusmod tempor incididunt ut labore et dolore</p>
  </div>
  <div class="service" style="left:363px">
    <div class="service-icon"><svg width="64" height="64" viewBox="0 0 64 64" fill="none" stroke="#1e9fdb" stroke-width="2.5"><circle cx="32" cy="32" r="10"/><circle cx="32" cy="32" r="18" stroke-dasharray="6 5"/></svg></div>
    <div class="service-title">Project Management</div>
    <p class="service-text">Lorem ipsum dolor sit amet, consectetur adipiscing elit, sed do eiusmod tempor incididunt ut labore et dolore</p>
  </div>
  <div class="service" style="left:617px">
    <div class="service-icon"><svg width="64" height="64" viewBox="0 0 64 64" fill="none" stroke="#1e9fdb" stroke-width="2.5"><path d="M14 14 L50 50M50 14 L14 50"/><circle cx="14" cy="14" r="5"/><circle cx="50" cy="50" r="5"/></svg></div>
    <div class="service-title">Major Equipment and Services Installation &amp; Commissioning</div>
    <p class="service-text">Lorem ipsum dolor sit amet, consectetur adipiscing elit, sed do eiusmod tempor incididunt ut labore et dolore</p>
  </div>
  <div class="service" style="left:872px">
    <div class="service-icon"><svg width="64" height="64" viewBox="0 0 64 64" fill="none" stroke="#1e9fdb" stroke-width="2.5"><path d="M14 34 A18 18 0 0 1 50 34Z"/><path d="M10 34h44M20 42h24v8H20z"/></svg></div>
    <div class="service-title">Engineering &amp; Maintenance Management</div>
    <p class="service-text">Lorem ipsum dolor sit amet, consectetur adipiscing elit, sed do eiusmod tempor incididunt ut labore et dolore</p>
  </div>
  <span class="btn btn-solid" style="left:517px;top:430px;width:167px">View All Services</span>
</section>

<section class="projects">
  <h2 class="section-title abs center">Our Projects</h2>
  <p class="projects-intro">Sed ut perspiciatis unde omnis iste natus error sit voluptatem accusantium doloremque laudantium, totam rem aperiam, eaque ipsa quae ab illo inventore veritatis et quasi architecto beatae vitae dicta sunt explicabo</p>
  <div class="project-tile" style="left:111px;top:192px;background:linear-gradient(135deg,#d9dde2,#8f969e)" role="img" aria-label="Photo of a plumber installing pipework beside a toilet with tools on the floor"></div>
  <div class="project-tile" style="left:443px;top:192px;background:linear-gradient(135deg,#e8eaec,#5a5f66)" role="img" aria-label="Photo of hands typing on a laptop keyboard at a desk"></div>
  <div class="project-tile" style="left:775px;top:192px;background:linear-gradient(135deg,#c9d7e6,#9aa6b3)" role="img" aria-label="Photo of a technician in protective wear operating stainless steel food processing equipment"></div>
  <div class="project-tile" style="left:111px;top:463px;background:linear-gradient(135deg,#e3e5e7,#8a8f95)" role="img" aria-label="Overhead photo of a team working at a desk with laptops"></div>
  <div class="project-tile" style="left:443px;top:463px;background:linear-gradient(135deg,#eef1f4,#a9b3bd)" role="img" aria-label="Photo of a bright modern glass-roofed building interior"></div>
  <div class="project-tile" style="left:775px;top:463px;background:linear-gradient(135deg,#e6e6e6,#c2c4c6)" role="img" aria-label="Image of an engineer in a hard hat beside a model of city buildings"></div>
  <span class="btn btn-light" style="left:534px;top:791px;width:132px">View More</span>
</section>

<section class="reviews">
  <h2 class="section-title abs center">Client Reviews</h2>
  <div class="avatar" role="img" aria-label="Portrait photo of the reviewing client"></div>
  <span class="quote-mark" style="left:198px;top:278px">&ldquo;</span>
  <p class="quote-text">At vero eos et accusamus et iusto odio dignissimos ducimus qui blanditiis praesentium voluptatum deleniti atque corrupti quos dolores et quas molestias excepturi sint occaecati cupiditate non provident, similique sunt in culpa qui officia deserunt mollitia animi, id est laborum et dolorum fuga. Et harum quidem rerum facilis est et expedita distinctio</p>
  <span class="quote-mark" style="left:962px;top:336px">&rdquo;</span>
  <div class="reviewer">
    <div class="reviewer-name">Occaecat Cupidatat</div>
    <div class="reviewer-role">(Eius modi tempora incidunt)</div>
  </div>
  <div class="dots"><span class="on"></span><span></span><span></span><span></span></div>
</section>

<footer class="site-footer">
  <div class="footer-brand"><span class="brand-mark"></span><span class="brand-name">Valtrix Engineering</span></div>
  <div class="socials"><span></span><span></span><span></span></div>

  <h3 class="footer-heading" style="left:533px">Links</h3>
  <div class="footer-links" style="left:533px">Home<br>About Us<br>Services<br>Projects</div>
  <div class="footer-links" style="left:713px">Terms of Use<br>Testimonials<br>Contact Us</div>

  <h3 class="footer-heading" style="left:903px">Contact Details</h3>
  <div class="contact">
    <div class="contact-row" style="line-height:22px"><svg width="10" height="14" viewBox="0 0 10 14" style="margin-top:4px;flex:none"><path d="M5 0a5 5 0 0 0-5 5c0 4 5 9 5 9s5-5 5-9a5 5 0 0 0-5-5z" fill="#fff"/><circle cx="5" cy="5" r="2" fill="#1b1b1d"/></svg><span>Ut enim ad minim veniam, quis nostrud exercitation</span></div>
    <div class="contact-row contact-strong" style="margin-top:10px"><svg width="13" height="13" viewBox="0 0 24 24" style="margin-top:4px"><path d="M6.6 10.8a15 15 0 0 0 6.6 6.6l2.2-2.2a1 1 0 0 1 1-.25 11.4 11.4 0 0 0 3.6.57 1 1 0 0 1 1 1V20a1 1 0 0 1-1 1A17 17 0 0 1 3 4a1 1 0 0 1 1-1h3.5a1 1 0 0 1 1 1c0 1.25.2 2.45.57 3.6a1 1 0 0 1-.25 1z" fill="#fff"/></svg><span>012 345 6789</span></div>
    <div class="contact-row contact-strong" style="margin-top:8px"><svg width="13" height="13" viewBox="0 0 24 24" style="margin-top:5px"><rect x="2" y="5" width="20" height="14" fill="#fff"/><path d="M2 5l10 8 10-8" fill="none" stroke="#1b1b1d" stroke-width="2"/></svg><span>info@domainname.com</span></div>
  </div>

  <div class="footer-rule"></div>
  <p class="copyright">Copyright © 2021 Corlett Associates. All rights reserved.</p>
</footer>

</body>
</html>
```